Create book cover for a Sudoku puzzle book

It is a sudoku puzzle book for experienced sudoku puzzle solvers. It has over 250 sudoku puzzles ranging from medium level to hard.

Create a book cover closely refer to the reference image. The book cover must look as similar to the reference image as possible, including all the design style, color, illustrations and fonts. Use the sudoku puzzle in the attachment to replace the one on the reference image. All the design elements including fonts must be commercially licensed.

In the final delivery, the cover design must be available in both png/ai and pdf file format. All source files and commercial licenses for the used design elements must also be delivered as well.

Book Title: Quill Harbor Puzzlers
Subtitle: 250+ Medium to Hard Puzzles

Book size: 8.5x11 inches
Page count: 171
Paperback Print Book
Platform: Brindlewood BPP

Text on the front cover (all in uppercase):
- Quill Harbor Puzzlers
- 250+ Medium to Hard Puzzles
- 2025
- 250+ Puzzles
- large print

Text on spine:
Book title (only title, no subtitle) on the upper part of the spine and author name on the lower part. All in uppercase.

Text on the back cover (on the top):
Thank you for purchasing "Quill Harbor Puzzlers." We hope you are enjoying the puzzles and finding them both challenging and fun. If you have a moment, please consider leaving a review on Brindlewood. Your feedback helps other puzzle enthusiasts discover this book and allows us to continue creating quality content. We appreciate your support and look forward to hearing your thoughts!

Logo on back cover:
-pen name logo, the logo size should be small and subtle. (on bottom middle)

```html
<!DOCTYPE html>
<html lang="en">
<head>
<meta charset="UTF-8">
<title>Quill Harbor Puzzlers – Cover Wrap</title>
<link rel="stylesheet" href="https://fonts.googleapis.com/css2?family=Poppins:wght@500;600;700;800;900&family=Raleway:ital,wght@0,500;0,600;1,500&display=swap">
<style>
  :root{
    --stage:#939393;
    --paper:#ffffff;
    --ink:#0e171d;
    --red:#e8363a;
    --badge-dark:#e06a00;
    --badge-light:#ffc21a;
    --logo-navy:#1f2c44;
  }
  *{box-sizing:border-box;margin:0;padding:0}
  html,body{width:1200px;height:800px;overflow:hidden;background:var(--stage)}
  .wrap{position:relative;width:1200px;height:800px}

  /* back cover */
  .back-cover{position:absolute;left:43px;top:72px;width:505px;height:655px;background:var(--paper);box-shadow:0 2px 6px rgba(0,0,0,.25)}
  .back-message{position:absolute;left:44px;top:44px;width:418px;font-family:"Raleway",sans-serif;font-weight:500;font-size:19.5px;line-height:24px;color:var(--ink);text-align:justify}
  .back-message em{font-style:italic}
  .pen-name{position:absolute;left:0;right:0;top:550px;display:flex;align-items:center;justify-content:center;gap:8px}
  .pen-name-dot{width:14px;height:14px;border-radius:50%;background:var(--logo-navy)}
  .pen-name-text{font-family:"Raleway",sans-serif;font-weight:600;font-size:15px;letter-spacing:.5px;color:var(--logo-navy)}

  /* spine */
  .spine{position:absolute;left:588px;top:72px;width:23px;height:655px;background:var(--paper);box-shadow:0 2px 6px rgba(0,0,0,.25)}
  .spine-title,.spine-author{position:absolute;left:0;width:23px;writing-mode:vertical-rl;font-family:"Poppins",sans-serif;font-size:15.5px;line-height:23px;color:var(--ink);text-align:center;white-space:nowrap}
  .spine-title{top:89px;font-weight:800}
  .spine-author{top:427px;font-weight:500;letter-spacing:.5px}

  /* front cover */
  .front-cover{position:absolute;left:651px;top:72px;width:505px;height:655px;background:var(--paper);overflow:hidden;box-shadow:0 2px 6px rgba(0,0,0,.25)}
  .splash-art{position:absolute;left:0;top:148px;width:505px;height:532px}
  .count-line{position:absolute;left:0;right:0;top:8px;text-align:center;font-family:"Poppins",sans-serif;font-weight:800;color:var(--ink);font-size:30px;line-height:44px}
  .count-line .count{color:var(--red);font-size:39px;letter-spacing:-1px}
  .main-title{position:absolute;left:0;right:0;top:48px;text-align:center;font-family:"Poppins",sans-serif;font-weight:900;font-size:55px;line-height:62px;letter-spacing:-1px;color:var(--ink)}
  .sub-title{position:absolute;left:0;right:0;top:116px;text-align:center;font-family:"Poppins",sans-serif;font-weight:800;font-size:28px;line-height:34px;color:var(--ink)}
  .year-tag{position:absolute;left:205px;top:158px;width:95px;height:32px;border-radius:9px;background:var(--red);color:#fff;font-family:"Poppins",sans-serif;font-weight:700;font-size:26px;line-height:32px;text-align:center}

  .puzzle-grid{position:absolute;left:160px;top:270px;width:176px;height:174px;border-collapse:collapse;background:#fff;border:2px solid var(--ink);font-family:"Poppins",sans-serif;font-weight:500;font-size:15px;color:var(--ink)}
  .puzzle-grid td{width:19.5px;height:19.3px;border:1px solid var(--ink);text-align:center;padding:0;line-height:19px}
  .puzzle-grid td:nth-child(3),.puzzle-grid td:nth-child(6){border-right:2px solid var(--ink)}
  .puzzle-grid tr:nth-child(3) td,.puzzle-grid tr:nth-child(6) td{border-bottom:2px solid var(--ink)}

  .print-badge{position:absolute;left:359px;top:460px;width:120px;height:120px}
  .bottom-band{position:absolute;left:0;bottom:0;width:505px;height:48px;background:var(--ink);color:#fff;font-family:"Poppins",sans-serif;font-weight:800;font-size:24.5px;line-height:48px;text-align:center;white-space:nowrap}
</style>
</head>
<body>
<div class="wrap">

  <section class="back-cover">
    <p class="back-message">Thank you for purchasing <em>"Quill Harbor Puzzlers"</em>. We hope you are enjoying the puzzles and finding them both challenging and fun. If you have a moment, please consider leaving a review on Brindlewood. Your feedback helps other puzzle enthusiasts discover this book and allows us to continue creating quality content. We appreciate your support and look forward to hearing your thoughts!</p>
    <div class="pen-name">
      <span class="pen-name-dot"></span>
      <span class="pen-name-text">ELIAS VANTREE</span>
    </div>
  </section>

  <section class="spine">
    <div class="spine-title">QUILL HARBOR PUZZLERS</div>
    <div class="spine-author">ELIAS VANTREE</div>
  </section>

  <section class="front-cover">
    <svg class="splash-art" role="img" aria-label="Explosive abstract paint splash in red, black and white radiating from the centre" viewBox="0 0 505 532">
      <defs>
        <radialGradient id="splashTone" cx="50%" cy="52%" r="62%">
          <stop offset="0" stop-color="#ffffff"/>
          <stop offset="0.3" stop-color="#d83a3f"/>
          <stop offset="0.55" stop-color="#1a1a1c"/>
          <stop offset="0.8" stop-color="#c9252b"/>
          <stop offset="1" stop-color="#ffffff"/>
        </radialGradient>
      </defs>
      <rect width="505" height="532" fill="url(#splashTone)"/>
    </svg>

    <div class="count-line"><span class="count">250+</span> PUZZLES</div>
    <h1 class="main-title">QUILL HARBOR</h1>
    <h2 class="sub-title">PUZZLERS</h2>
    <div class="year-tag">2025</div>

    <table class="puzzle-grid" aria-label="Sudoku puzzle">
      <tr><td></td><td></td><td>4</td><td></td><td>7</td><td></td><td></td><td></td><td>2</td></tr>
      <tr><td>6</td><td></td><td></td><td>1</td><td></td><td></td><td></td><td>4</td><td></td></tr>
      <tr><td></td><td>9</td><td></td><td></td><td></td><td>2</td><td>5</td><td></td><td></td></tr>
      <tr><td></td><td></td><td>9</td><td></td><td>6</td><td></td><td></td><td></td><td>3</td></tr>
      <tr><td>4</td><td></td><td></td><td>8</td><td></td><td></td><td></td><td>9</td><td></td></tr>
      <tr><td></td><td></td><td>3</td><td></td><td></td><td>4</td><td>8</td><td></td><td></td></tr>
      <tr><td></td><td>6</td><td></td><td></td><td>3</td><td></td><td></td><td></td><td>4</td></tr>
      <tr><td></td><td></td><td>7</td><td>4</td><td></td><td></td><td>6</td><td></td><td></td></tr>
      <tr><td>3</td><td></td><td></td><td></td><td>8</td><td></td><td></td><td>7</td><td></td></tr>
    </table>

    <svg class="print-badge" viewBox="0 0 120 120" aria-label="Large print">
      <defs>
        <radialGradient id="badgeTone" cx="50%" cy="45%" r="55%">
          <stop offset="0" stop-color="#ffc21a"/>
          <stop offset="1" stop-color="#e06a00"/>
        </radialGradient>
      </defs>
      <polygon fill="#ffffff" points="60,0 66,8 75,2 78,12 88,9 88,19 98,19 95,29 105,32 99,40 108,46 100,52 106,60 100,68 108,74 99,80 105,88 95,91 98,101 88,101 88,111 78,108 75,118 66,112 60,120 54,112 45,118 42,108 32,111 32,101 22,101 25,91 15,88 21,80 12,74 20,68 14,60 20,52 12,46 21,40 15,32 25,29 22,19 32,19 32,9 42,12 45,2 54,8"/>
      <circle cx="60" cy="60" r="47" fill="url(#badgeTone)"/>
      <g transform="rotate(8 60 60)" font-family="Poppins, sans-serif" fill="#111" text-anchor="middle">
        <text x="60" y="57" font-size="21" font-weight="800">LARGE</text>
        <text x="60" y="80" font-size="21" font-weight="600">PRINT</text>
      </g>
    </svg>

    <div class="bottom-band">250+ MEDIUM TO HARD PUZZLES</div>
  </section>

</div>
</body>
</html>
```